Corvane Holdings , new business card design

investment firm with corporate clients . need double sided business card , vertical and horizontal options ,logo must be clear. prefer pantone colors only and sharp design. website also www.corvane.ae

Khalid Bin Tarrafi
Managing Director
Tel. +971 4 387 2940
Mobile +971 50 518 2403
khalid@corvane.ae
Q-Span Plaza, officw 18-B07, Warqa Gardens, Dubai

Contact Information for Business Card

Khalid Bin Tarrafi
Managing Director

Font styles to use
Serif

Colors

Designer to choose colors to be used in the design.

```html
<!DOCTYPE html>
<html lang="en">
<head>
<meta charset="utf-8">
<title>Corvane Holdings – Business Card</title>
<link rel="stylesheet" href="https://fonts.googleapis.com/css2?family=Montserrat:wght@700&family=Questrial&display=swap">
<style>
  :root {
    --backdrop: #666666;
    --paper: #ffffff;
    --brand-blue: #47719a;
    --name-blue: #3b6a9c;
    --ink: #222222;
    --rule: #c9c9c9;
  }
  * { margin: 0; padding: 0; box-sizing: border-box; }
  html, body {
    width: 1200px; height: 802px; overflow: hidden;
    background: var(--backdrop);
    font-family: "Questrial", sans-serif;
  }
  .stage { position: relative; width: 1200px; height: 802px; }

  .card {
    position: absolute; top: 274px;
    width: 443px; height: 265px;
  }
  .card--front { left: 136px; background: var(--paper); color: var(--ink); }
  .card--back  { left: 624px; background: var(--brand-blue); color: var(--paper); }

  .wordmark { position: absolute; text-align: center; line-height: 1; }
  .wordmark__name { display: block; letter-spacing: 0.42em; margin-right: -0.42em; }
  .wordmark__sub  { display: block; letter-spacing: 0.62em; margin-right: -0.62em; }

  .card--front .wordmark { left: 20px; top: 112px; width: 192px; color: var(--ink); }
  .card--front .wordmark__name { font-size: 25px; }
  .card--front .wordmark__sub  { font-size: 9px; margin-top: 7px; }

  .divider {
    position: absolute; left: 230px; top: 58px;
    width: 1px; height: 143px; background: var(--rule);
  }

  .contact { position: absolute; left: 244px; top: 76px; }
  .contact__name {
    font-family: "Montserrat", sans-serif; font-weight: 700;
    font-size: 13.5px; color: var(--name-blue); white-space: nowrap;
  }
  .contact__role { font-size: 12.5px; margin-top: 2px; }
  .contact__list { list-style: none; margin-top: 16px; }
  .contact__item {
    display: flex; align-items: center; gap: 6px;
    font-size: 12.5px; line-height: 15.7px; white-space: nowrap;
  }
  .contact__icon { width: 9px; height: 9px; fill: var(--name-blue); flex: none; }

  .address {
    position: absolute; left: 0; right: 0; top: 211px;
    text-align: center; font-size: 12.5px;
  }

  .card--back .wordmark { left: 0; right: 0; top: 104px; }
  .card--back .wordmark__name { font-size: 38px; }
  .card--back .wordmark__sub  { font-size: 13px; margin-top: 10px; }
  .website {
    position: absolute; left: 0; right: 0; top: 209px;
    text-align: center; font-size: 12.5px; letter-spacing: 0.14em;
  }
</style>
</head>
<body>
<main class="stage">

  <section class="card card--front" aria-label="Card front">
    <div class="wordmark">
      <span class="wordmark__name">CORVANE</span>
      <span class="wordmark__sub">HOLDINGS</span>
    </div>

    <div class="divider"></div>

    <div class="contact">
      <p class="contact__name">KHALID BIN TARRAFI</p>
      <p class="contact__role">Managing Director</p>
      <ul class="contact__list">
        <li class="contact__item">
          <svg class="contact__icon" viewBox="0 0 10 10" aria-hidden="true"><path d="M0 3.2C0 1.6 2 1 5 1s5 .6 5 2.2V4H7.2V3H2.8v1H0zM2 4.6h6l1.4 4.4H.6z"/></svg>
          +971 4 387 2940
        </li>
        <li class="contact__item">
          <svg class="contact__icon" viewBox="0 0 10 10" aria-hidden="true"><path d="M2.5 0h5a.8.8 0 0 1 .8.8v8.4a.8.8 0 0 1-.8.8h-5a.8.8 0 0 1-.8-.8V.8A.8.8 0 0 1 2.5 0zm.4 1.2v6.6h4.2V1.2z"/></svg>
          +971 50 518 2403
        </li>
        <li class="contact__item">
          <svg class="contact__icon" viewBox="0 0 10 10" aria-hidden="true"><path d="M0 2h10v.8L5 5.8 0 2.8zm0 2 5 3 5-3v4H0z"/></svg>
          khalid@corvane.ae
        </li>
        <li class="contact__item">
          <svg class="contact__icon" viewBox="0 0 10 10" aria-hidden="true"><circle cx="5" cy="5" r="5"/><path d="M3 3.2h2.2l.8 1.6-1.4 1.2.4 2.2L3.6 6.6 2.6 4.4z" fill="#fff"/></svg>
          www.corvane.ae
        </li>
      </ul>
    </div>

    <p class="address">Q-Span Plaza, officw 18-B07 Warqa Gardens, Dubai</p>
  </section>

  <section class="card card--back" aria-label="Card back">
    <div class="wordmark">
      <span class="wordmark__name">CORVANE</span>
      <span class="wordmark__sub">HOLDINGS</span>
    </div>
    <p class="website">www.corvane.ae</p>
  </section>

</main>
</body>
</html>
```